Vantrel System Web Page Design

This project is to design 6 pages of a web based medical system for clinics, hospitals, drugs suppliers, general items suppliers, insurance company, laboratories and patients (basically all parties which could be involved in).We want the designs of the browser, button, icon and layout are based on Zeltor, which is user friendly, looks professional, simple and neat but with powerful functions. We have uploaded few pictures of another system, please do not copy its design because this is not what we are looking for, the pictures are for you to know the elements should be included in our pages. Vantrel web-base system, design 6 pages1. Login PageShould include the following elements-company id with input field-login id with input field-password with input field2. Main Page (Navigation page)Should include the following elements-Appointment-Consultation-Patient-Drugs inventory -General supplies inventory -Laboratory-Suppliers-Insurance-Reports 3. Appointment PageShould include all the the elements in the respective pictures plus the followings-Daily View, Weekly View, Monthly View buttons4. Consultation PageShould include all the the elements in the respective picture5. Patient Page5.1 General information Should include all the the elements in the respective picture5.2 medical history/lab reportsShould include all the the elements in the respective picture plus the followings-Notify patient button-Share report button.
Updated on 28 Nov:
Please stop using Harbor Suite in your designs which is not the name of our system. We have just rename our system to Vantrel, please take note.
We need the system to look professional not playful, do not use too many colors and playful icons.

```html
<!DOCTYPE html>
<html lang="en">
<head>
<meta charset="UTF-8">
<title>Vantrel System – Login</title>
<link rel="stylesheet" href="https://fonts.googleapis.com/css2?family=Arimo:wght@400;500&display=swap">
<style>
  :root {
    --page-bg: #e1e1e1;
    --chrome-top: #ececec;
    --chrome-bottom: #dcdcdc;
    --chrome-border: #a9a9a9;
    --chrome-text: #3a3a3a;
    --panel-top: #2a7cc3;
    --panel-bottom: #1f6aae;
    --text-light: #ffffff;
    --text-muted: #a8d0f3;
    --field-bg: #ffffff;
    --field-border: #1b4f80;
    --light-close: #e0443e;
    --light-min: #dea123;
    --light-max: #1aab29;
  }
  * { box-sizing: border-box; margin: 0; padding: 0; }
  html, body {
    width: 1200px; height: 761px; overflow: hidden;
    background: var(--page-bg);
    font-family: "Arimo", "Helvetica Neue", Arial, sans-serif;
  }
  .app-window {
    position: absolute; left: 37px; top: 60px;
    width: 1128px; height: 641px;
    border: 1px solid var(--chrome-border);
    border-radius: 6px; overflow: hidden;
    box-shadow: 0 14px 30px rgba(0,0,0,0.28);
    background: linear-gradient(180deg, var(--panel-top), var(--panel-bottom));
  }
  .title-bar {
    position: relative; height: 31px;
    background: linear-gradient(180deg, var(--chrome-top), var(--chrome-bottom));
    border-bottom: 1px solid #b5b5b5;
  }
  .traffic-lights { position: absolute; left: 12px; top: 7px; display: flex; gap: 11px; }
  .light { width: 17px; height: 17px; border-radius: 50%; border: 1px solid rgba(0,0,0,0.25); }
  .light.close { background: var(--light-close); }
  .light.minimize { background: var(--light-min); }
  .light.maximize { background: var(--light-max); }
  .window-title {
    text-align: center; line-height: 31px;
    font-size: 17px; color: var(--chrome-text);
  }
  .expand-icon { position: absolute; right: 8px; top: 7px; }
  .app-name {
    position: absolute; left: 14px; top: 44px;
    font-size: 35px; font-weight: 400; color: var(--text-light);
  }
  .emblem {
    position: absolute; left: 530px; top: 155px;
    width: 139px; height: 110px;
    border-radius: 50%;
    background: rgba(255,255,255,0.12);
  }
  .login-heading {
    position: absolute; left: 0; right: 0; top: 285px;
    text-align: center; font-size: 26px; color: var(--text-light);
  }
  .login-form { position: absolute; left: 0; top: 347px; width: 100%; }
  .form-row { position: absolute; left: 0; width: 100%; height: 30px; }
  .form-row label {
    position: absolute; right: 693px; top: 5px;
    font-size: 18px; color: var(--text-light); white-space: nowrap;
  }
  .form-row input {
    position: absolute; left: 447px; top: 0;
    width: 232px; height: 30px;
    border: 1px solid var(--field-border); border-radius: 4px;
    background: var(--field-bg);
    box-shadow: inset 0 1px 2px rgba(0,0,0,0.2);
  }
  .row-company { top: 0; }
  .row-login { top: 44px; }
  .row-password { top: 88px; }
  .submit-button {
    position: absolute; left: 519px; top: 133px;
    width: 88px; height: 30px;
    border: 1px solid #8a8a8a; border-radius: 5px;
    background: linear-gradient(180deg, #ffffff, #e4e4e4);
    font-family: inherit; font-size: 17px; color: #111;
  }
  .footer {
    position: absolute; right: 14px; bottom: 14px;
    font-size: 15px; letter-spacing: 0.6px; color: var(--text-muted);
    display: flex; gap: 16px;
  }
  .footer a { color: inherit; text-decoration: none; }
  .footer .divider { opacity: 0.5; }
</style>
</head>
<body>
  <div class="app-window">
    <div class="title-bar">
      <div class="traffic-lights">
        <span class="light close"></span>
        <span class="light minimize"></span>
        <span class="light maximize"></span>
      </div>
      <div class="window-title">Vantrel System</div>
      <svg class="expand-icon" width="18" height="18" viewBox="0 0 18 18" fill="none" stroke="#8a8a8a" stroke-width="2">
        <path d="M10 2h6v6M16 2l-6 6M8 16H2v-6M2 16l6-6"/>
      </svg>
    </div>

    <h1 class="app-name">Vantrel System</h1>

    <div class="emblem" role="img" aria-label="Heart with pulse line emblem"></div>

    <h2 class="login-heading">Login to Vantrel System</h2>

    <form class="login-form">
      <div class="form-row row-company">
        <label for="company-id">Company ID:</label>
        <input id="company-id" type="text">
      </div>
      <div class="form-row row-login">
        <label for="login-id">Login ID:</label>
        <input id="login-id" type="text">
      </div>
      <div class="form-row row-password">
        <label for="password">Password:</label>
        <input id="password" type="password">
      </div>
      <button class="submit-button" type="button">Submit</button>
    </form>

    <div class="footer">
      <a href="#">Forgot Vantrel System ID or Password?</a>
      <span class="divider">|</span>
      <span>Copyright © 2018 Vantrel System. All Rights Reserved.</span>
    </div>
  </div>
</body>
</html>
```